Varnik Holdings — Business Card Design Brief
Overview
Design a double-sided business card for Varnik Holdings that highlights our two service arms: Varnik Communications (telecommunications) and Varnik Energy (business energy solutions). The card should feel smart and stand out when handed to clients.

Objectives
Showcase our areas of specialty clearly.
Reflect the overall Varnik / Varnik Holdings brand while acknowledging both arms.
Explore using both logos (Communications + Energy) or one unified logo, depending on the design.

Deliverables
One double-sided business card design (front + back).

Content & Copy
Front (preferred): Logo: Varnik / Varnik Holdings
Descriptor: Business Communications | Business Energy
Back:My contact details and company details
Core products: Business Mobile • Telephony • Internet • Business Energy Solutions

Brand & Visual Direction
We have a group logo currently tailored more toward telecoms, plus a separate Varnik Energy logo.
Please explore layouts that use both logos or just one, whichever works best.
Color: I wouldn't mind seeing an option using our the Blue/Purple gradient from our website (varnik-example.co.uk), but also open to non-gradient approaches and other colours..

Overall look: Smart, modern, and distinctive.
Format & Print Specs
Double-sided business card format. (Use a standard size

Must-Haves
Front: Varnik wording or Varnik Holdings wording with atleast 1 logo also on front “Business Communications | Business Energy.”

Back: Contact + company details and core products.
A design that stands out while remaining professional.

Nice-to-Have Options
A gradient version using our site’s Blue/Purple gradient.
A non-gradient version.
A dual-logo treatment versus a single-logo treatment.

Thanks
Owen

```html
<!DOCTYPE html>
<html lang="en">
<head>
<meta charset="utf-8">
<title>Varnik Holdings – Business Card</title>
<link href="https://fonts.googleapis.com/css2?family=Roboto:wght@300;400;500;700;900&display=swap" rel="stylesheet">
<style>
  :root{
    --bg:#ececec;
    --card:#ffffff;
    --navy:#2b2878;
    --blue:#1f6fd6;
    --blue-deep:#1a52c9;
    --cyan:#36b6e6;
    --purple-line:#3a2f8f;
    --green:#5cb832;
    --lime:#c9d618;
    --text-grey:#6b6b6b;
    --rule:#8a8a8a;
  }
  *{box-sizing:border-box;margin:0;padding:0}
  html,body{width:1200px;height:900px;overflow:hidden;background:var(--bg);font-family:'Roboto',sans-serif}
  .canvas{position:relative;width:1200px;height:900px}
  .card{position:absolute;width:560px;height:320px;background:var(--card);border-radius:22px;overflow:hidden;
        box-shadow:0 14px 30px rgba(0,0,0,.18)}
  .card--front{left:30px;top:290px}
  .card--back{left:610px;top:290px}

  /* shared wordmark */
  .wordmark{display:flex;align-items:center;gap:12px}
  .wordmark__dot{border-radius:50%;flex:none}
  .wordmark__name{font-weight:900;color:var(--navy);letter-spacing:1px;line-height:1}

  /* front */
  .contact{position:absolute;left:34px;top:28px;width:200px}
  .contact__name{font-size:19px;font-weight:700;color:var(--blue);letter-spacing:.5px}
  .contact__role{font-size:13px;color:var(--text-grey);margin-top:2px}
  .contact__rule{height:1px;background:var(--rule);margin:8px 0;width:100%}
  .contact__list{list-style:none;font-size:13px;color:var(--text-grey);line-height:1.55}
  .contact__list li{display:flex;align-items:center;gap:7px;white-space:nowrap}
  .contact__list svg{width:11px;height:11px;flex:none}

  .front-brand{position:absolute;right:40px;top:100px}
  .front-brand .wordmark__dot{width:46px;height:46px;background:var(--blue)}
  .front-brand .wordmark__name{font-size:54px}
  .front-brand__rule{position:absolute;right:30px;top:172px;width:290px;height:1px;background:var(--rule)}
  .address{position:absolute;right:40px;top:184px;text-align:right;font-size:15px;color:var(--text-grey);line-height:1.35}

  .band{position:absolute;left:0;right:0;bottom:0;height:62px;
        background:linear-gradient(90deg,var(--blue-deep),var(--cyan));
        border-top:4px solid var(--purple-line);display:flex;align-items:center;padding-left:34px}
  .band__text{color:#fff;font-size:16px;font-weight:400;letter-spacing:.3px}

  /* back */
  .back-brand{position:absolute;left:40px;top:70px}
  .back-brand .wordmark__dot{width:38px;height:38px;background:var(--green)}
  .back-brand .wordmark__name{font-size:40px}
  .divider{position:absolute;left:262px;top:50px;width:1px;height:110px;background:var(--rule)}
  .products{position:absolute;left:288px;top:56px;list-style:none;font-size:16px;color:var(--text-grey);line-height:1.5}
  .products li{display:flex;align-items:center;gap:7px}
  .products li::before{content:"";width:7px;height:7px;border-radius:50%;background:var(--green)}
  .back-band{position:absolute;left:0;right:0;bottom:0;height:110px;
        background:linear-gradient(90deg,var(--lime),var(--green))}
</style>
</head>
<body>
<div class="canvas">

  <section class="card card--front" aria-label="Business card front">
    <div class="contact">
      <p class="contact__name">DANIEL HARPER</p>
      <p class="contact__role">Managing Director</p>
      <div class="contact__rule"></div>
      <ul class="contact__list">
        <li><svg viewBox="0 0 12 12"><circle cx="6" cy="6" r="6" fill="#1f6fd6"/><path d="M3.5 3.5c.5 2.5 2.5 4.5 5 5l.8-1-1.3-.8-.6.6c-1-.5-1.8-1.3-2.3-2.3l.6-.6-.8-1.3z" fill="#fff"/></svg>044-555 010 203</li>
        <li><svg viewBox="0 0 12 12"><circle cx="6" cy="6" r="6" fill="#1f6fd6"/><rect x="3" y="4" width="6" height="4.2" fill="none" stroke="#fff" stroke-width=".9"/><path d="M3 4l3 2.3L9 4" fill="none" stroke="#fff" stroke-width=".9"/></svg>info@varnik-example.co.uk</li>
        <li><svg viewBox="0 0 12 12"><circle cx="6" cy="6" r="6" fill="#1f6fd6"/><circle cx="6" cy="6" r="3" fill="none" stroke="#fff" stroke-width=".9"/><path d="M3 6h6M6 3v6" stroke="#fff" stroke-width=".7"/></svg>www.varnik-example.co.uk</li>
      </ul>
    </div>

    <div class="front-brand">
      <div class="wordmark">
        <span class="wordmark__name">VARNIK</span>
        <span class="wordmark__dot"></span>
      </div>
    </div>
    <div class="front-brand__rule"></div>
    <p class="address">Your Address, City<br>State, Zip 0000</p>

    <div class="band"><span class="band__text">Business Communications | Business Energy</span></div>
  </section>

  <section class="card card--back" aria-label="Business card back">
    <div class="back-band" role="img" aria-label="Decorative lime to green sweep with a blue accent"></div>

    <div class="back-brand">
      <div class="wordmark">
        <span class="wordmark__name">VARNIK</span>
        <span class="wordmark__dot"></span>
      </div>
    </div>
    <div class="divider"></div>
    <ul class="products">
      <li>Business Mobile</li>
      <li>Telephony</li>
      <li>Internet</li>
      <li>Business Energy Solutions</li>
    </ul>
  </section>

</div>
</body>
</html>
```